Elegant Business Card with Logo and Picture

Please create a business card that has the Logo colors add Gold and turquoise / use the attached logo - I would like a beautiful Business Card - Please make sure it's printed on both sides / Picture can go on one side Logo other
www.velmoragrove.com
614-372-0583
Lina Suzette Brolin
linasb@quorvamail.com
Life Coach
Thessing Certified Teacher / Life Coach / Interior Designer
Transformational Retreats

Target Market(s)

Women Men General

Industry/Entity Type

Life Coaching

Contact Information for Business Card

www.velmoragrove.com
614-372-0583
Lina Suzette Brolin
Life Coach
Thessing Certified Teacher / Yoga Teacher / Interior Designer

Font styles to use
Serif
Decorative

Colors
33a6d6
e34197
ffc214

Requirements
Must have
• Quality Paper and touch /
Nice to have
• Beautiful Touch and feel
Should not have
• needs to be elegant

```html
<!DOCTYPE html>
<html lang="en">
<head>
<meta charset="utf-8">
<title>Velmora Grove Coaching – Business Card</title>
<link href="https://fonts.googleapis.com/css2?family=Open+Sans:wght@400;600;700&family=Roboto:wght@500;700&display=swap" rel="stylesheet">
<style>
  :root {
    --backdrop: #1e1e1e;
    --card-white: #ffffff;
    --pink-start: #ff0a5a;
    --pink-end: #f00080;
    --ink: #141414;
    --text-light: #ffffff;
    --photo-tone-a: #f3e6da;
    --photo-tone-b: #d9b27a;
  }
  * { box-sizing: border-box; margin: 0; padding: 0; }
  html, body {
    width: 1200px; height: 800px; overflow: hidden;
    background: var(--backdrop);
  }
  .stage {
    position: relative; width: 1200px; height: 800px;
    display: flex; flex-direction: column; align-items: center; justify-content: center;
    gap: 40px;
  }
  .card {
    position: relative; width: 560px; height: 320px;
    border-radius: 18px; overflow: hidden;
  }
  .card--front { background: var(--card-white); }
  .brand {
    position: absolute; inset: 0;
    display: flex; align-items: center; justify-content: center;
  }
  .brand__name {
    font-family: "Open Sans", sans-serif; font-weight: 600;
    font-size: 20px; letter-spacing: 3px; text-transform: uppercase;
    color: var(--ink);
  }
  .card--back {
    background: linear-gradient(100deg, var(--pink-start) 0%, var(--pink-end) 100%);
  }
  .portrait {
    position: absolute; top: 28px; right: 30px;
    width: 190px; height: 220px; border-radius: 26px;
    background: linear-gradient(180deg, var(--card-white) 0%, var(--photo-tone-a) 45%, var(--photo-tone-b) 100%);
  }
  .details {
    position: absolute; left: 62px; bottom: 34px;
    color: var(--text-light); font-family: "Open Sans", sans-serif;
  }
  .details__name {
    font-family: "Roboto", sans-serif; font-weight: 700;
    font-size: 21px; margin-bottom: 4px;
  }
  .details__roles { font-size: 11.5px; line-height: 1.4; margin-left: 10px; margin-bottom: 10px; }
  .contact { list-style: none; margin-left: 20px; font-size: 11.5px; line-height: 1.55; }
  .contact__item { display: flex; align-items: center; gap: 8px; }
  .contact__icon { width: 11px; height: 11px; fill: var(--text-light); flex: none; }
</style>
</head>
<body>
<main class="stage">
  <section class="card card--front" aria-label="Card front">
    <div class="brand">
      <span class="brand__name">Velmora Grove Coaching</span>
    </div>
  </section>

  <section class="card card--back" aria-label="Card back">
    <div class="portrait" role="img" aria-label="Portrait photo of Lina Suzette Brolin"></div>
    <div class="details">
      <h1 class="details__name">Lina Suzette Brolin</h1>
      <p class="details__roles">Life Coach<br>Thessing Certified Teacher<br>Yoga Teacher / Interior Designer</p>
      <ul class="contact">
        <li class="contact__item">
          <svg class="contact__icon" viewBox="0 0 24 24" aria-hidden="true"><path d="M6.6 10.8a15.1 15.1 0 0 0 6.6 6.6l2.2-2.2c.3-.3.7-.4 1-.2 1.1.4 2.3.6 3.6.6.6 0 1 .4 1 1V20c0 .6-.4 1-1 1A17 17 0 0 1 3 4c0-.6.4-1 1-1h3.5c.6 0 1 .4 1 1 0 1.3.2 2.5.6 3.6.1.3 0 .7-.2 1l-2.3 2.2z"/></svg>
          <span>614-372-0583</span>
        </li>
        <li class="contact__item">
          <svg class="contact__icon" viewBox="0 0 24 24" aria-hidden="true"><path d="M2 5h20v14H2z M3 6l9 7 9-7" stroke="#ff0a5a" stroke-width="1.5"/></svg>
          <span>linasb@quorvamail.com</span>
        </li>
        <li class="contact__item">
          <svg class="contact__icon" viewBox="0 0 24 24" aria-hidden="true"><circle cx="12" cy="12" r="10"/><path d="M2 12h20M12 2c3 3 3 17 0 20M12 2c-3 3-3 17 0 20" stroke="#ff0a5a" stroke-width="1.5" fill="none"/></svg>
          <span>www.velmoragrove.com</span>
        </li>
      </ul>
    </div>
  </section>
</main>
</body>
</html>
```